Church Website with Home Page and Member Sermon Library

I am in need of an updated design for our church website. This will include 4 pages (outlined below). We are a conservative, evangelical, Christian church. The site should be modern and clean, while still reflecting our conservative values. I already have a logo for our church, and I want the site to incorporate the logo, and match the logo/branding. Stock photos are allowed if needed, but I have uploaded some images of our church and would prefer those images to be used if possible. Any stock photos used should not include any people in the photos (scenery, nature, buildings, animals, etc. are fine).

The site will need 4 pages: Home, Support Us (Donate), Login, and Recording Library.

Page 1: Home
The home page should include the following sections:

- Navigation: Should include links to each section of the home page plus a "listen live" link which will take the user to a live-streaming site and a "support us" link which will take the user to a support/donate page.

- Announcements: Can be either a banner or some other design, but there needs to be some way for us to post announcements for visitors to see. I'm open for creative ideas in this section, but would like it not to take up a lot of room on the page.

- About Us: Should include address, service times (see attached document), and information about the church.

- Pastor Bio: A section that introduces our pastor and gives a short bio about our pastor. Would like this section to include a picture of our pastor. Somewhere in this section I would like to include this Bible reference: "And I will give you pastors according to mine heart, which shall feed you with knowledge and understanding. Jer 3:15 LPW"

- Articles of Faith (What We Believe): This should include several sub-sections each with a heading, body, and possibly 1 or more scripture references. I have attached a document to the brief that includes our articles of faith. Feel free to be creative with this section in how you lay these out and format them.

- Support Us: A small section that explains what kind of support someone can give and a link to a donation page. The link can say something like "Support Us" or "Donate Now".

- Contact form: A contact form that allows the visitor to send us a message. The contact form should ask for name, email, phone, and message.

- Footer: A footer that will be displayed on all pages of the site. This should include at a minimum a link to the home page (or a link to each individual section in the home page if you prefer), a link to "listen live", a link to "support us", a link to "contact us" (or you can put the contact form directly in the footer if you prefer), the address, and a "member login" link.

Page 2: Support Us
The donation page should include a form the visitor can fill out to make a donation. We will embed a third party form later. For this design, please just mock out the design with a basic form asking for name, phone, and email.

Page 3: Login
The recording library (detailed below) will require members to login with a shared numeric code before accessing the page. We need a design for a login screen. The screen should include navigation/footer just like all other pages, but the body of the login page will consist only of a form that asks the user to enter the access code and then a "login" button.

Page 4: Recording Library

The library page is a member-only page that will require a shared, numeric pass code to access. On this page, members will be able to access a filterable list of past sermons. The page by default should display most recent sermons, but should also include a search form that allows the member to filter the sermon list to find a particular sermon. The search form should allow the user to select a filter type (e.g. Speaker name, date, event, etc.) and type in a value to search. They should be able to add multiple filters and remove filters that have been added. Each sermon that is displayed in the result list should include basic information such as title, date, speaker, tags, etc. along with a download icon, and an embedded audio player where they can click a play button to stream it on-demand. Each sermon should also have clickable tags associated with it that can be used to find related sermons.
Updates

I have uploaded several images of our church. Feel free to incorporate these into your design if possible.

Target Market(s)

Church Members

Industry/Entity Type

Religion

Number of Pages Required

4 page

Font styles to use
Sans Serif

Colors

Designer to choose colors to be used in the design.

Requirements
Must have
• Must incorporate the logo (attached)
Nice to have
• Would like the design to incorporate pictures of our church (attached) instead of stock photos if possible.
Should not have
• Please avoid an overly cluttered design. Stock photos used should not include any people in the photos.

```html
<!DOCTYPE html>
<html lang="en">
<head>
<meta charset="utf-8">
<title>Donation – Grace Covenant Church</title>
<link href="https://fonts.googleapis.com/css2?family=Cinzel:wght@400;500&family=Montserrat:wght@400;500;600;700&display=swap" rel="stylesheet">
<style>
:root{
  --sage:#83a86f;
  --sage-dark:#6e9160;
  --ink:#1c1c1c;
  --muted:#555;
  --line:#dcdcdc;
  --footer:#2e2e2e;
  --footer-text:#cfcfcf;
  --navy:#1d2a4a;
  --cream:#f4f1ec;
}
*{box-sizing:border-box;margin:0;padding:0}
html,body{width:712px;height:1200px;overflow:hidden;background:#fff}
body{position:relative;font-family:"Montserrat",sans-serif;color:var(--ink)}
.abs{position:absolute}

/* hero */
.hero{left:0;top:0;width:712px;height:270px;
  background:linear-gradient(180deg,#ffffff 0%,rgba(255,255,255,.6) 14%,rgba(255,255,255,0) 30%),
  linear-gradient(180deg,#f4efe7 0%,#f1e8dc 55%,#d9b48a 80%,#b5814f 100%)}
.brand{left:92px;top:28px;width:110px;text-align:center;font-family:"Cinzel",serif;color:var(--sage);font-size:11px;line-height:13px;letter-spacing:1px}
.brand-mark{display:block;margin:0 auto 4px;width:12px;height:12px;border-radius:50%;background:var(--sage)}
.nav{top:20px;right:106px;display:flex;gap:33px;font-size:9px;color:#2a2a2a}
.page-title{left:0;width:712px;top:140px;text-align:center;font-family:"Cinzel",serif;font-size:35px;letter-spacing:3px;color:#111}
.rule-thick{left:307px;top:188px;width:97px;height:2px;background:#111}
.rule-thin{left:332px;top:192px;width:47px;height:1px;background:#111}

/* form */
.login-note{left:159px;top:311px;font-size:9px}
.panel{left:159px;width:395px;border:1px solid var(--line)}
.panel-title{position:absolute;left:21px;font-size:8px;letter-spacing:1px;font-weight:500}
.field-label{position:absolute;font-size:8px;letter-spacing:.8px;color:#444}
.input{position:absolute;height:27px;border:1px solid var(--line);background:#fff;font-size:8px;color:#aaa;padding:9px 10px}
.amount{position:absolute;top:30px;width:114px;height:27px;border:1px solid var(--line);font-size:8px;letter-spacing:.6px;color:#555;display:flex;align-items:center;justify-content:center}
.amount.selected{background:var(--sage);border-color:var(--sage);color:#fff;font-weight:700}
.radio{position:absolute;left:23px;width:10px;height:10px;border:1px solid #333;border-radius:50%}
.radio.on{border-color:var(--sage)}
.radio.on::after{content:"";position:absolute;left:2px;top:2px;width:4px;height:4px;border-radius:50%;background:var(--sage)}
.method{position:absolute;left:40px;font-size:8px;font-weight:600;color:var(--navy)}
.method-note{position:absolute;left:40px;top:58px;width:150px;font-size:7px;line-height:12px;color:#555}
.card-badge{position:absolute;top:125px;width:21px;height:15px;border-radius:2px}
.support-btn{left:160px;top:901px;width:89px;height:26px;background:var(--sage);color:#fff;font-family:"Cinzel",serif;font-size:9px;display:flex;align-items:center;justify-content:center;gap:5px}

/* footer */
.footer{left:0;top:971px;width:712px;height:229px;background:var(--footer)}
.listen{left:106px;top:1041px;width:131px;height:39px;border-radius:20px;background:var(--cream);border:2px solid var(--sage);box-shadow:0 6px 12px rgba(0,0,0,.35);display:flex;align-items:center}
.listen-dot{width:35px;height:35px;border-radius:50%;background:var(--sage);margin-left:1px}
.listen span{margin-left:11px;font-family:"Cinzel",serif;font-size:9px;color:var(--sage);font-weight:500}
.f-heading{font-family:"Cinzel",serif;font-size:9.5px;letter-spacing:1px;color:#e6e6e6}
.f-text{font-size:8px;color:var(--footer-text);line-height:10px}
.footer-brand{left:256px;top:1080px;width:200px;text-align:center;font-family:"Cinzel",serif;font-size:16px;line-height:18px;letter-spacing:1.5px;color:var(--sage)}
.footer-brand .brand-mark{width:16px;height:16px;margin-bottom:8px}
.quick{left:490px;top:1046px}
.quick ul{list-style:none;margin-top:10px}
.quick li{font-size:8px;color:var(--footer-text);height:16.4px}
.divider{left:0;top:1159px;width:712px;height:1px;background:#3b3b3b}
.copy{left:105px;top:1172px;font-size:7px;color:#ddd}
.social{top:1173px;display:flex;gap:10px;left:543px}
.social i{display:block;width:7px;height:7px;border-radius:50%;background:#ddd}
</style>
</head>
<body>

<header>
  <div class="abs hero" role="img" aria-label="Sanctuary interior with wooden pews and hymn boards, softly lit"></div>
  <div class="abs brand"><span class="brand-mark"></span>Grace Covenant<br>Church</div>
  <nav class="abs nav"><span>About Us</span><span>Articles Of Faith</span><span>Contact Us</span></nav>
  <h1 class="abs page-title">DONATION</h1>
  <div class="abs rule-thick"></div>
  <div class="abs rule-thin"></div>
</header>

<main>
  <p class="abs login-note">Registered before? Log in to use your saved details.</p>

  <section class="abs panel" style="top:334px;height:126px">
    <h2 class="panel-title" style="top:15px">YOUR DONATION</h2>
    <div class="amount" style="left:21px">$20,00</div>
    <div class="amount selected" style="left:140px">$50,00</div>
    <div class="amount" style="left:259px">$100,00</div>
    <h2 class="panel-title" style="top:69px">CUSTOM AMOUNT</h2>
    <div class="input" style="left:21px;top:84px;width:355px">$0,00</div>
  </section>

  <section class="abs panel" style="top:470px;height:245px">
    <h2 class="panel-title" style="top:15px">DETAILS</h2>
    <label class="field-label" style="left:21px;top:37px">First name *</label>
    <label class="field-label" style="left:202px;top:37px">Last name *</label>
    <div class="input" style="left:21px;top:50px;width:171px"></div>
    <div class="input" style="left:202px;top:50px;width:171px"></div>
    <label class="field-label" style="left:21px;top:88px">Email *</label>
    <label class="field-label" style="left:202px;top:88px">Phone</label>
    <div class="input" style="left:21px;top:101px;width:171px"></div>
    <div class="input" style="left:202px;top:101px;width:171px"></div>
    <label class="field-label" style="left:21px;top:139px">Address</label>
    <div class="input" style="left:21px;top:152px;width:352px"></div>
    <label class="field-label" style="left:21px;top:190px">City</label>
    <label class="field-label" style="left:202px;top:190px">Postcode</label>
    <div class="input" style="left:21px;top:203px;width:171px"></div>
    <div class="input" style="left:202px;top:203px;width:171px"></div>
  </section>

  <section class="abs panel" style="top:725px;height:161px">
    <h2 class="panel-title" style="top:15px">CHOOSE YOUR PAYMENT METHOD</h2>
    <span class="radio" style="top:42px"></span>
    <span class="method" style="top:43px">QuickPay</span>
    <p class="method-note">You'll be forwarded to QuickPay to complete your payment.</p>
    <span class="radio on" style="top:105px"></span>
    <span class="method" style="top:106px">Credit / Debit Card</span>
    <span class="card-badge" style="left:42px;background:#1f5fb8"></span>
    <span class="card-badge" style="left:67px;background:#2b3a63"></span>
  </section>

  <a class="abs support-btn">
    <svg width="12" height="12" viewBox="0 0 12 12" fill="none" stroke="#fff" stroke-width=".8"><circle cx="7" cy="6" r="3"/><path d="M1 10h6l3-2"/><path d="M1 8h3"/></svg>
    SUPPORT US
  </a>
</main>

<footer>
  <div class="abs footer"></div>
  <div class="abs listen"><div class="listen-dot"></div><span>LISTEN LIVE</span></div>
  <div class="abs" style="left:110px;top:1099px">
    <h3 class="f-heading">LOCATION</h3>
    <div style="display:flex;gap:4px;margin-top:8px">
      <svg width="7" height="9" viewBox="0 0 7 9" fill="none" stroke="#83a86f" stroke-width=".8"><path d="M3.5 8.5C1.5 6 .5 4.7.5 3.4a3 3 0 0 1 6 0c0 1.3-1 2.6-3 5.1z"/><circle cx="3.5" cy="3.4" r="1"/></svg>
      <p class="f-text">418 Meadow Lane, Fairview,<br>Ohio 40210</p>
    </div>
  </div>
  <div class="abs footer-brand"><span class="brand-mark"></span>GRACE COVENANT<br>CHURCH</div>
  <div class="abs quick">
    <h3 class="f-heading">QUICK LINKS</h3>
    <ul><li>About Us</li><li>Articles Of Faith</li><li>Support Our Ministry</li><li>Contact Us</li><li>Member Login</li></ul>
  </div>
  <div class="abs divider"></div>
  <p class="abs copy">Copyright 2023 Grace Covenant Church I All rights reserved</p>
  <div class="abs social"><i></i><i></i><i></i><i></i></div>
</footer>

</body>
</html>
```